Mastering Modern Vineyard Management

size of the ad - 8”x 10.75" plus 0.25" bleed
I would like an ad for a magazine that will stand out and make people want to read the ad.
The ad should not be crowded and people reading the ad will be able to read the text.
I would like it to be a creative and modern-day design.
the list of topics should not be the focus of the ad.
the text is attached.
If you decide to use people in the ad then please no ladies.
please note that leave over 1 inch for the bottom of the footer

```html
<!DOCTYPE html>
<html lang="en">
<head>
<meta charset="utf-8">
<title>Mastering Modern Vineyard Management – Course Ad</title>
<link href="https://fonts.googleapis.com/css2?family=Oswald:wght@300;400;500&family=Yellowtail&family=Roboto+Condensed:wght@400;500&display=swap" rel="stylesheet">
<style>
  :root {
    --backdrop: #e2e2e2;
    --paper: #f4f4f4;
    --ink: #1c1c1c;
    --band-dark: #262626;
    --accent-red: #dc2a30;
    --white: #ffffff;
    --sky-top: #b9cbdc;
    --sky-low: #e7ecf1;
    --wall: #f1f2f3;
    --lawn: #8c8f5e;
  }
  * { margin: 0; padding: 0; box-sizing: border-box; }
  html, body {
    width: 1200px; height: 873px; overflow: hidden;
    background: var(--backdrop);
  }
  .ad-page {
    position: absolute;
    left: 290px; top: 26px;
    width: 620px; height: 820px;
    background: var(--paper);
    overflow: hidden;
    box-shadow: 0 6px 22px rgba(0,0,0,0.12);
  }
  .hero-photo {
    position: absolute; left: 0; top: 0;
    width: 620px; height: 500px;
    background:
      linear-gradient(180deg, transparent 62%, rgba(140,143,94,0.55) 82%, var(--lawn) 100%),
      linear-gradient(180deg, var(--sky-top) 0%, var(--sky-low) 38%, var(--wall) 60%);
  }
  .course-title {
    position: absolute; right: 28px; top: 26px;
    text-align: right;
    font-family: "Oswald", sans-serif;
    font-weight: 400;
    color: var(--ink);
    line-height: 0.9;
    letter-spacing: 1px;
  }
  .course-title .title-line { display: block; font-size: 72px; }
  .course-title .title-script {
    position: absolute;
    left: -118px; bottom: 6px;
    font-family: "Yellowtail", cursive;
    color: var(--accent-red);
    font-size: 52px;
    letter-spacing: 0;
    transform: rotate(-6deg);
  }
  .schedule-band {
    position: absolute;
    left: 250px; top: 388px;
    width: 370px; height: 112px;
    background: var(--band-dark);
    color: var(--white);
    font-family: "Oswald", sans-serif;
    font-weight: 400;
    font-size: 19px;
    letter-spacing: 2.5px;
    line-height: 1.35;
    text-align: center;
    padding-top: 16px;
  }
  .offer-band {
    position: absolute;
    left: 0; top: 500px;
    width: 620px; height: 150px;
    background: var(--accent-red);
    color: var(--white);
    padding: 26px 34px 0;
  }
  .offer-headline {
    font-family: "Oswald", sans-serif;
    font-weight: 500;
    font-size: 18px;
    letter-spacing: 1.5px;
    line-height: 1.3;
    text-transform: uppercase;
  }
  .topic-list {
    margin-top: 12px;
    font-family: "Roboto Condensed", sans-serif;
    font-size: 12px;
    line-height: 1.45;
    opacity: 0.92;
  }
</style>
</head>
<body>
  <main class="ad-page">
    <div class="hero-photo" role="img" aria-label="Photo of a modern white building with a paved path and lawn under a pale blue sky"></div>

    <h1 class="course-title">
      <span class="title-line">VINEYARD</span>
      <span class="title-line">MANAGEMENT</span>
      <span class="title-script">course</span>
    </h1>

    <section class="schedule-band">
      <p>STARTING FEB.28</p>
      <p>MONDAY 10 AM – TUESDAY</p>
      <p>EVENINGS SESSIONS</p>
    </section>

    <section class="offer-band">
      <p class="offer-headline">Early bird special for those that started<br>or would like to go into vineyard management</p>
      <p class="topic-list">
        Site selection | Vineyard investment strategies | Due diligence<br>
        Financing | Crop planning | Canopy management | Wine law basics<br>
        Sourcing vines | Harvest logistics | Dealing with buyers | Tax fundamentals
      </p>
    </section>
  </main>
</body>
</html>
```